KR Appraisals website redesign

I would like to refresh my existing website of www.krappraisals-example.com with new graphics, look and feel, as well as updated structure and wording. Content and layout changes have been uploaded to this project Brief.

My existing website has a dark feel. I am now looking for a light and energetic feel. Financial Services is my industry, so the website should be reflect that. I would also like to reflect the concepts of Trust, Service and Expertise.

The website must be serious and upmarket.

Target Market(s)

Corporate board members, CFO's, treasurers and controllers
Auditors, tax advisors, private equity and venture capital asset managers, investors, tax authorities

Industry/Entity Type

Financial Service

Coding

Coded - Design and coding required

Number of Pages Required

5+ page

Font styles to use
Sans Serif
Other font styles liked:
• Designer can choose another modern font

Colors
0355a3
3277b5
85acd3
eaf1f7
f37122
f68d4d
9bcb3c
acd037
cadf82

Requirements
Must have
• Good hi resolution pictures that convey "Finance", "Trust", "Service" or "Expertise".
• An anti-bot (such as Captcha) mechanism in the contact form.
Should not have
• Must not have all content on one rolling screen.

```html
<!DOCTYPE html>
<html lang="en">
<head>
<meta charset="utf-8">
<title>KR Appraisals – Contact</title>
<link href="https://fonts.googleapis.com/css2?family=Figtree:wght@400;500;600;700&display=swap" rel="stylesheet">
<style>
:root{
  --blue:#0355a3;
  --orange:#f37122;
  --green:#9bcb3c;
  --text:#444;
  --muted:#888;
  --grey-bg:#f1f1f1;
  --dark:#333;
  --line:#555;
  --map-a:#e6e9ec;
  --map-b:#d3dde6;
}
*{margin:0;padding:0;box-sizing:border-box}
html,body{width:848px;height:1200px;overflow:hidden;background:#fff;font-family:"Figtree",sans-serif;color:var(--text)}
.page{position:relative;width:848px;height:1200px}
.abs{position:absolute}
.site-header{left:0;top:0;width:848px;height:71px;background:linear-gradient(90deg,#e4e6dc,#eeefe5 50%,#f4f5e4)}
.brand{display:flex;align-items:center;gap:5px;font-weight:500;letter-spacing:.5px;white-space:nowrap}
.brand .mark{width:8px;height:8px;background:currentColor}
.header-brand{left:114px;top:26px;font-size:15px;color:#777}
.main-nav{top:31px;font-size:8px;font-weight:600;color:#777;letter-spacing:.1px}
.main-nav.active{color:var(--blue)}
.section-title{left:0;width:848px;text-align:center;color:var(--orange);font-weight:700;letter-spacing:.3px}
.intro{left:0;width:848px;text-align:center;font-size:8px;line-height:14px;color:#555}
.contact-icon{width:53px;height:53px;border-radius:50%;background:var(--blue);display:flex;align-items:center;justify-content:center}
.contact-label{font-size:8.5px;font-weight:600;color:var(--green)}
.contact-value{font-size:8px;font-weight:600;color:#333}
.map{width:223px;height:143px;background:linear-gradient(135deg,var(--map-a),var(--map-b))}
.office{width:223px;text-align:center}
.office h3{font-size:10.5px;font-weight:600;color:var(--orange);margin-bottom:8px}
.office p{font-size:7.5px;color:var(--muted);line-height:13px}
.office .tel{margin-top:6px;font-size:8px;font-weight:600;color:var(--blue)}
.office svg,.foot-col svg{vertical-align:-1px;margin-right:4px}
.touch{left:0;top:595px;width:848px;height:405px;background:var(--grey-bg)}
.field{background:#fff;border:1px solid #e2e2e2;font-size:7.5px;color:var(--muted);padding:10px 7px 0}
.send{left:366px;top:854px;width:116px;height:32px;background:var(--orange);color:#fff;font-size:7.5px;font-weight:700;display:flex;align-items:center;justify-content:center;letter-spacing:.3px}
.footer-bg{left:0;top:950px}
.footer-brand{left:0;width:848px;top:990px;justify-content:center;font-size:16px;color:#999}
.rule{left:114px;width:621px;height:1px;background:var(--line)}
.foot-nav{top:1063px;font-size:8px;font-weight:600;color:#999}
.foot-nav.active{color:var(--green)}
.foot-col{top:1105px;font-size:7.5px;color:#aaa;line-height:15px}
.foot-col h4{font-size:9px;font-weight:600;color:var(--orange);margin-bottom:6px}
.foot-col .hl{color:var(--green)}
.foot-col .wh{color:#eee}
.badge{background:#555;border-radius:4px}
</style>
</head>
<body>
<div class="page">

  <header class="abs site-header"></header>
  <div class="abs brand header-brand"><span class="mark"></span>KR APPRAISALS</div>
  <nav>
    <span class="abs main-nav" style="left:432px">HOME</span>
    <span class="abs main-nav" style="left:485px">ABOUT</span>
    <span class="abs main-nav" style="left:542px">SERVICES</span>
    <span class="abs main-nav" style="left:608px">NEWS &amp; VIEWS</span>
    <span class="abs main-nav active" style="left:696px">CONTACT</span>
  </nav>

  <h1 class="abs section-title" style="top:132px;font-size:27px">CONTACT</h1>
  <p class="abs intro" style="top:165px">Please do not hesitate to contact us by phone, email, post or by completing form on the right hand side of this page.<br>We look forward to hearing from you.</p>

  <div class="abs contact-icon" style="left:196px;top:228px">
    <svg width="22" height="22" viewBox="0 0 24 24"><path fill="#fff" d="M6.6 10.8a15.1 15.1 0 0 0 6.6 6.6l2.2-2.2c.3-.3.7-.4 1-.2 1.1.4 2.3.6 3.6.6.6 0 1 .4 1 1V20c0 .6-.4 1-1 1A17 17 0 0 1 3 4c0-.6.4-1 1-1h3.5c.6 0 1 .4 1 1 0 1.3.2 2.5.6 3.6.1.3 0 .7-.2 1z"/></svg>
  </div>
  <div class="abs contact-label" style="left:261px;top:239px">PHONE</div>
  <div class="abs contact-value" style="left:261px;top:254px">+31 70 555 0142 | | +31 20 555 0187</div>

  <div class="abs contact-icon" style="left:445px;top:228px">
    <svg width="26" height="20" viewBox="0 0 26 20"><rect x="1" y="1" width="24" height="18" rx="3" fill="#fff"/><path d="M2 3l11 8 11-8" fill="none" stroke="var(--blue)" stroke-width="2.2"/></svg>
  </div>
  <div class="abs contact-label" style="left:510px;top:239px">EMAIL</div>
  <div class="abs contact-value" style="left:510px;top:254px">info@krappraisals-example.com</div>

  <div class="abs map" style="left:190px;top:310px" role="img" aria-label="Street map of the Leiden office location"></div>
  <div class="abs map" style="left:435px;top:310px" role="img" aria-label="Street map of the Amsterdam office location"></div>

  <div class="abs office" style="left:190px;top:466px">
    <h3>LEIDEN</h3>
    <p><svg width="7" height="10" viewBox="0 0 10 14"><path fill="var(--green)" d="M5 0a5 5 0 0 0-5 5c0 3.8 5 9 5 9s5-5.2 5-9a5 5 0 0 0-5-5zm0 7a2 2 0 1 1 0-4 2 2 0 0 1 0 4z"/></svg>Kanaalweg 48, 2321 AB Leiden<br>The Netherlands</p>
    <div class="tel"><svg width="9" height="9" viewBox="0 0 24 24"><path fill="var(--green)" d="M6.6 10.8a15.1 15.1 0 0 0 6.6 6.6l2.2-2.2c.3-.3.7-.4 1-.2 1.1.4 2.3.6 3.6.6.6 0 1 .4 1 1V20c0 .6-.4 1-1 1A17 17 0 0 1 3 4c0-.6.4-1 1-1h3.5c.6 0 1 .4 1 1 0 1.3.2 2.5.6 3.6.1.3 0 .7-.2 1z"/></svg>070 555 0142</div>
  </div>
  <div class="abs office" style="left:435px;top:466px">
    <h3>AMSTERDAM</h3>
    <p><svg width="7" height="10" viewBox="0 0 10 14"><path fill="var(--green)" d="M5 0a5 5 0 0 0-5 5c0 3.8 5 9 5 9s5-5.2 5-9a5 5 0 0 0-5-5zm0 7a2 2 0 1 1 0-4 2 2 0 0 1 0 4z"/></svg>Zuidplein 17, 1077 XV Amsterdam<br>The Netherlands</p>
    <div class="tel"><svg width="9" height="9" viewBox="0 0 24 24"><path fill="var(--green)" d="M6.6 10.8a15.1 15.1 0 0 0 6.6 6.6l2.2-2.2c.3-.3.7-.4 1-.2 1.1.4 2.3.6 3.6.6.6 0 1 .4 1 1V20c0 .6-.4 1-1 1A17 17 0 0 1 3 4c0-.6.4-1 1-1h3.5c.6 0 1 .4 1 1 0 1.3.2 2.5.6 3.6.1.3 0 .7-.2 1z"/></svg>020 555 0187</div>
  </div>

  <section class="abs touch"></section>
  <h2 class="abs section-title" style="top:647px;font-size:27px">GET IN TOUCH WITH US</h2>
  <div class="abs field" style="left:196px;top:706px;width:223px;height:26px">Name</div>
  <div class="abs field" style="left:429px;top:706px;width:223px;height:26px">Company Name</div>
  <div class="abs field" style="left:196px;top:743px;width:223px;height:27px">Email</div>
  <div class="abs field" style="left:429px;top:743px;width:223px;height:27px">Phone</div>
  <div class="abs field" style="left:196px;top:780px;width:456px;height:64px">Comments</div>
  <div class="abs send">SEND MESSAGE</div>

  <svg class="abs footer-bg" width="848" height="250" viewBox="0 0 848 250"><polygon points="0,49 424,0 848,49 848,250 0,250" fill="var(--dark)"/></svg>
  <div class="abs brand footer-brand"><span class="mark"></span>KR APPRAISALS</div>
  <div class="abs rule" style="top:1053px"></div>
  <span class="abs foot-nav active" style="left:273px">HOME</span>
  <span class="abs foot-nav" style="left:326px">ABOUT</span>
  <span class="abs foot-nav" style="left:383px">SERVICES</span>
  <span class="abs foot-nav" style="left:449px">NEWS &amp; VIEWS</span>
  <span class="abs foot-nav" style="left:537px">CONTACT</span>
  <div class="abs rule" style="top:1085px"></div>

  <div class="abs foot-col" style="left:115px">
    <h4>CREDITS</h4>
    © 2019 <span class="hl">KR Appraisals</span><br>
    Logo by <span class="wh">Lotte Verhagen</span><br>
    Website by <span class="hl">Northline Web Studio</span>
  </div>
  <div class="abs foot-col" style="left:275px">
    <h4>LEIDEN</h4>
    <svg width="7" height="10" viewBox="0 0 10 14"><path fill="var(--green)" d="M5 0a5 5 0 0 0-5 5c0 3.8 5 9 5 9s5-5.2 5-9a5 5 0 0 0-5-5zm0 7a2 2 0 1 1 0-4 2 2 0 0 1 0 4z"/></svg>Kanaalweg 48<br><span style="padding-left:14px">2321 AB Leiden</span><br>
    <span class="wh" style="display:block;margin-top:5px"><svg width="9" height="9" viewBox="0 0 24 24"><path fill="var(--green)" d="M6.6 10.8a15.1 15.1 0 0 0 6.6 6.6l2.2-2.2c.3-.3.7-.4 1-.2 1.1.4 2.3.6 3.6.6.6 0 1 .4 1 1V20c0 .6-.4 1-1 1A17 17 0 0 1 3 4c0-.6.4-1 1-1h3.5c.6 0 1 .4 1 1 0 1.3.2 2.5.6 3.6.1.3 0 .7-.2 1z"/></svg>070 555 0142</span>
  </div>
  <div class="abs foot-col" style="left:436px">
    <h4>AMSTERDAM</h4>
    <svg width="7" height="10" viewBox="0 0 10 14"><path fill="var(--green)" d="M5 0a5 5 0 0 0-5 5c0 3.8 5 9 5 9s5-5.2 5-9a5 5 0 0 0-5-5zm0 7a2 2 0 1 1 0-4 2 2 0 0 1 0 4z"/></svg>Zuidplein 17<br><span style="padding-left:14px">1077 XV Amsterdam</span><br>
    <span class="wh" style="display:block;margin-top:5px"><svg width="9" height="9" viewBox="0 0 24 24"><path fill="var(--green)" d="M6.6 10.8a15.1 15.1 0 0 0 6.6 6.6l2.2-2.2c.3-.3.7-.4 1-.2 1.1.4 2.3.6 3.6.6.6 0 1 .4 1 1V20c0 .6-.4 1-1 1A17 17 0 0 1 3 4c0-.6.4-1 1-1h3.5c.6 0 1 .4 1 1 0 1.3.2 2.5.6 3.6.1.3 0 .7-.2 1z"/></svg>020 555 0187</span>
  </div>

  <div class="abs badge" style="left:604px;top:1100px;width:120px;height:24px" role="img" aria-label="Professional institute membership badge"></div>
  <div class="abs badge" style="left:604px;top:1132px;width:120px;height:50px" role="img" aria-label="Appraisers society membership badge"></div>

</div>
</body>
</html>
```